Retail Jewelry Business Card Design Project

We are in need of a new business card design for a retail jewelry store. This store is in the business of fine jewelry including but not specific to bridal jewelry, diamonds, designer jewelry and watches.

This store has been in business for 20 years but continues to strive for a modern professional appeal. The main colors use for this business are a royal blue, white and silver.

Target Market(s)

Target market is ages 18-50

Industry/Entity Type

Jewelry

Requirements
Must have
• Sales Person Name
Sales Person Email Address

Store Address
Store Phone
Website

Standard business card size. No odd shapes or sizes.
Nice to have
• Overall modern feel for card.

We have thought that a design with a nice feature of the logo on the back of the card would be nice but open to ideas.
Should not have
• No specific images of jewelry should be used.

```html
<!DOCTYPE html>
<html lang="en">
<head>
<meta charset="utf-8">
<title>Marlowe Reed Fine Jewelry – Business Card</title>
<link rel="stylesheet" href="https://fonts.googleapis.com/css2?family=Tinos:wght@400;700&family=Great+Vibes&family=Arimo:wght@400&display=swap">
<style>
  :root {
    --royal: #2e3192;
    --royal-light: #7a74c4;
    --paper: #ffffff;
    --stage: #ebeaf0;
    --ink-grey: #3c3c44;
    --card-edge: #d6d5de;
  }
  * { box-sizing: border-box; margin: 0; padding: 0; }
  html, body {
    width: 1200px; height: 980px; overflow: hidden;
    background: var(--stage);
  }
  .canvas { position: relative; width: 1200px; height: 980px; }

  .card {
    position: absolute;
    width: 700px; height: 400px;
    background: var(--paper);
    border-radius: 30px;
    overflow: hidden;
    box-shadow: 0 0 0 1px var(--card-edge), 0 14px 30px rgba(40, 40, 80, 0.12);
  }
  .card--front { left: 250px; top: 50px; }
  .card--back  { left: 250px; top: 520px; }

  .wordmark {
    position: absolute;
    color: var(--royal);
    font-family: "Tinos", "Times New Roman", serif;
    font-weight: 700;
    text-align: center;
    line-height: 1;
  }
  .wordmark__name { display: block; font-size: 64px; letter-spacing: 1px; }
  .wordmark__sub  { display: block; font-size: 28px; letter-spacing: 6px; margin-top: 14px; }

  .card--front .wordmark { left: 0; width: 700px; top: 34px; }
  .card--back  .wordmark { left: 0; width: 700px; top: 120px; }

  .band { position: absolute; left: 0; top: 0; width: 700px; height: 400px; }

  .person {
    position: absolute;
    right: 60px; top: 166px;
    font-family: "Great Vibes", cursive;
    font-size: 38px;
    color: var(--royal);
  }

  .contact {
    position: absolute;
    left: 34px; top: 246px;
    color: var(--paper);
    font-family: "Tinos", "Times New Roman", serif;
    font-size: 19px;
    line-height: 34px;
  }
  .contact__line { display: flex; align-items: center; gap: 9px; white-space: nowrap; }
  .contact__icon { width: 16px; height: 16px; flex: none; }

  .website {
    position: absolute;
    left: 0; width: 700px; top: 268px;
    text-align: center;
    font-family: "Arimo", Arial, sans-serif;
    font-size: 18px;
    letter-spacing: 4px;
    color: var(--ink-grey);
  }
</style>
</head>
<body>
<main class="canvas">

  <section class="card card--front" aria-label="Card front">
    <svg class="band" viewBox="0 0 700 400" aria-hidden="true">
      <path d="M0,192 Q480,200 712,400" fill="none" stroke="var(--royal-light)" stroke-width="3"/>
      <path d="M0,205 Q470,215 700,400 L0,400 Z" fill="var(--royal)"/>
    </svg>

    <div class="wordmark">
      <span class="wordmark__name">Marlowe Reed</span>
      <span class="wordmark__sub">FINE JEWELRY</span>
    </div>

    <p class="person">Marlowe Reed Halvorsen</p>

    <div class="contact">
      <p class="contact__line">
        <svg class="contact__icon" viewBox="0 0 16 16" aria-hidden="true">
          <circle cx="8" cy="8" r="7.5" fill="#fff"/>
          <path d="M5 4.2c.4-.3.9-.2 1.1.2l.8 1.4c.2.4.1.8-.2 1l-.6.5c.4.9 1.1 1.7 2 2.1l.5-.6c.3-.3.7-.4 1-.2l1.4.8c.4.2.5.7.2 1.1l-.5.7c-.4.5-1.1.7-1.7.4C7.6 10.8 5.2 8.4 4.3 6.1c-.2-.6 0-1.3.4-1.7z" fill="var(--royal)"/>
        </svg>
        555-014-2290
      </p>
      <p class="contact__line">
        <svg class="contact__icon" viewBox="0 0 16 16" aria-hidden="true">
          <circle cx="8" cy="8" r="7.5" fill="#fff"/>
          <rect x="3.8" y="5.2" width="8.4" height="5.6" fill="none" stroke="var(--royal)" stroke-width="1.1"/>
          <path d="M3.8 5.2 L8 8.4 L12.2 5.2" fill="none" stroke="var(--royal)" stroke-width="1.1"/>
        </svg>
        marlowe@marlowereedjewelry.com
      </p>
      <p class="contact__line">
        <svg class="contact__icon" viewBox="0 0 16 16" aria-hidden="true">
          <circle cx="8" cy="8" r="7.5" fill="#fff"/>
          <circle cx="8" cy="8" r="4.6" fill="none" stroke="var(--royal)" stroke-width="1"/>
          <ellipse cx="8" cy="8" rx="2" ry="4.6" fill="none" stroke="var(--royal)" stroke-width="1"/>
          <path d="M3.4 8h9.2" stroke="var(--royal)" stroke-width="1"/>
        </svg>
        www.marlowereedjewelry.com
      </p>
      <p class="contact__line">2870 Linden Avenue, Bayport, FL 32099</p>
    </div>
  </section>

  <section class="card card--back" aria-label="Card back">
    <div class="wordmark">
      <span class="wordmark__name">Marlowe Reed</span>
      <span class="wordmark__sub">FINE JEWELRY</span>
    </div>
    <p class="website">www.marlowereedjewelry.com</p>
  </section>

</main>
</body>
</html>
```